Financial & Tax Strategies

need to get a word press site with existing domains and condense existing content on existing site, make new site dynamic, need mobile too......need to take info from my quorvia website and get modern, relevant site, less verbose on first page, way more things to click and engage people. Would like it to look like this , but with my color scheme and not quite as busy looking. I like much of the content on my tabs. Want maximize by seo capabilities on their as well. The number one thing I can say is to go to my existing website and get content, logo, etc there … www.pinegatelarkgroup.com .

Target Market(s)

Those 40 -65, business owners for at least 5 years. Higher net worth.

Number of Pages Required

5+ page

Font styles to use
Sans Serif

Colors
f04a50
e4daeb
ffffff

Requirements
Must have
• seo maximized, lots of places to click on to contact us, calls to action, relevant, conservative, want it to look like this and have the function as well.....slight variation on messaging, but like the simplicity on first view. https://www.dorrickvale.com/
Nice to have
• Some area along right side where videos we do will be.
Should not have
• feel too busy, but still have lots of opportunities to engage.

```html
<!DOCTYPE html>
<html lang="en">
<head>
<meta charset="utf-8">
<title>Pinegate Lark Group</title>
<link href="https://fonts.googleapis.com/css2?family=Roboto:wght@400;500;700&family=Lato:wght@400;700&display=swap" rel="stylesheet">
<style>
:root{
  --red:#ed1c24;
  --red-soft:#f04a50;
  --lilac:#e4daeb;
  --white:#ffffff;
  --ink:#2b2b2b;
  --grey:#555;
  --band:#333333;
  --page:#f4f4f4;
  --line:#dddddd;
}
*{box-sizing:border-box;margin:0;padding:0}
html,body{width:1200px;height:3600px;overflow:hidden}
body{font-family:'Lato',Arial,sans-serif;color:var(--ink);background:var(--white);position:relative}
.site-header{height:96px;display:flex;align-items:center;justify-content:space-between;padding:0 60px 0 78px;background:var(--white);box-shadow:0 2px 6px rgba(0,0,0,.08);position:relative;z-index:2}
.menu-toggle span{display:block;width:24px;height:3px;background:var(--grey);margin:4px 0}
.brand{display:flex;align-items:center;gap:12px;font-family:'Roboto',Arial,sans-serif;font-weight:500;font-size:24px;line-height:1.05;color:#444}
.brand-dot{width:44px;height:44px;border-radius:50%;border:5px solid #555}
.header-call{display:flex;align-items:center;gap:10px;font-size:14px;line-height:1.3;color:#444}
.header-call b{color:var(--red);font-weight:400}
.phone-badge{width:30px;height:30px;border-radius:50%;background:var(--red);display:flex;align-items:center;justify-content:center;flex:none}
.hero{height:540px;position:relative;background:linear-gradient(135deg,#0b1a2e 0%,#14345a 45%,#0d1f38 100%);display:flex;align-items:center;justify-content:center}
.hero-title{background:rgba(20,30,45,.8);color:var(--white);font-family:'Roboto',Arial,sans-serif;font-size:34px;padding:36px 88px;margin-left:-40px}
.hero-arrow{position:absolute;top:50%;margin-top:-16px}
.hero-arrow.prev{left:38px}.hero-arrow.next{right:38px}
.dots{display:flex;gap:8px;justify-content:center}
.dots i{width:7px;height:7px;border-radius:50%;background:#bbb;display:block}
.dots i.on{background:var(--red)}
.hero .dots{position:absolute;bottom:20px;left:0;right:0}
.services{height:468px;display:flex;padding:60px 84px 0;gap:100px}
.services h2{font-family:'Roboto',Arial,sans-serif;font-weight:400;font-size:34px;margin-bottom:28px}
.service-list{list-style:none;font-size:15px;color:#444}
.service-list li{display:flex;align-items:center;gap:16px;height:36px}
.chart{width:516px;height:336px;margin-top:17px;background:var(--white);box-shadow:0 0 6px rgba(0,0,0,.12)}
.contact-band{height:196px;background:linear-gradient(90deg,#3a3a3a,#5a524c 50%,#3a3a3a);color:var(--white);text-align:center;font-family:'Roboto',Arial,sans-serif;padding-top:24px}
.contact-band h3{font-size:30px;font-weight:500}
.contact-row{display:flex;justify-content:center;gap:40px;margin:16px 0 10px;font-size:34px;font-weight:700}
.contact-row span{display:flex;align-items:center;gap:14px}
.contact-row .phone-badge{width:52px;height:52px}
.contact-band small{font-size:18px;font-weight:700}
.strategies{height:416px;background:var(--page);padding-top:50px;text-align:center}
.section-title{font-family:'Roboto',Arial,sans-serif;font-weight:400;font-size:32px;color:#333}
.strategy-grid{display:flex;gap:26px;justify-content:center;margin-top:56px}
.strategy-card{width:240px;height:221px;background:var(--white);border-radius:14px;display:flex;flex-direction:column;align-items:center;padding:64px 18px 0;font-size:16px;line-height:1.3;color:#444}
.strategy-card svg{margin-bottom:16px}
.dark-band{height:64px;background:var(--band);color:var(--white);display:flex;align-items:center;justify-content:center;font-family:'Roboto',Arial,sans-serif;font-size:32px}
.blogs{height:696px;background:var(--page);padding-top:48px}
.blog-grid{display:flex;gap:18px;justify-content:center}
.blog-card{width:346px;height:480px;background:var(--white);padding:12px;font-size:14px;line-height:1.35;color:#444}
.blog-media{height:212px;margin-bottom:22px}
.blog-card h4{font-family:'Roboto',Arial,sans-serif;font-size:17px;font-weight:700;color:#222;margin-bottom:6px}
.pill{display:inline-block;background:var(--red);color:var(--white);border-radius:22px;font-family:'Roboto',Arial,sans-serif;font-weight:500}
.blogs .pill{display:block;width:204px;margin:84px auto 0;text-align:center;padding:11px 0;font-size:16px}
.testimonials{height:676px;background:var(--page);padding-top:60px}
.testimonial-grid{display:flex;gap:30px;justify-content:center}
.testimonial{width:302px;height:336px;background:var(--white);border-radius:18px;text-align:center;padding:24px 22px 0;font-size:14px;line-height:1.3;color:#555}
.avatar{width:100px;height:100px;border-radius:50%;margin:0 auto 14px;background:radial-gradient(circle,#9aa3ad,#5d6670)}
.testimonial h5{font-family:'Roboto',Arial,sans-serif;font-size:17px;font-weight:500;color:#222;margin-bottom:16px}
.testimonials .dots{margin-top:30px}
.subscribe{display:flex;justify-content:center;margin-top:72px}
.subscribe .field{width:420px;height:42px;background:var(--white);border-radius:21px 0 0 21px;font-size:14px;color:#666;padding:12px 22px}
.subscribe .pill{width:160px;height:42px;display:flex;align-items:center;justify-content:center;margin-left:-10px;border-radius:21px;font-size:15px}
.call-us{display:flex;justify-content:center;align-items:center;gap:16px;margin-top:34px;font-family:'Roboto',Arial,sans-serif;font-weight:700;font-size:30px;color:#333}
.call-us .phone-badge{width:56px;height:56px}
.site-footer{height:319px;background:var(--band);color:#ddd;display:flex;padding:58px 0 0 77px;font-size:14px;line-height:1.45}
.footer-brand{width:326px}
.footer-brand .brand{color:var(--white);font-size:24px;margin-bottom:14px}
.footer-brand .brand-dot{border-color:var(--white)}
.footer-col h6{font-family:'Roboto',Arial,sans-serif;font-weight:400;font-size:17px;color:var(--white);margin-bottom:14px}
.links{width:168px}.links ul{padding-left:18px}
.address{width:252px}
.address p{display:flex;gap:8px}
.contact-form{width:293px}
.form-row{display:flex;gap:6px;margin-bottom:6px}
.form-row div,.form-msg{background:#111;color:#ddd;font-size:12px;padding:6px 8px;height:30px;flex:1}
.form-msg{height:72px;margin-bottom:14px}
.contact-form .pill{padding:8px 24px;font-size:13px}
.copyright{height:60px;background:var(--white);display:flex;align-items:center;justify-content:space-between;padding:0 78px;font-size:13px;color:#333}
.social{display:flex;gap:12px}
.social i{width:26px;height:26px;border-radius:50%;background:var(--red);display:block}
</style>
</head>
<body>
<header class="site-header">
  <div class="menu-toggle" aria-label="Menu"><span></span><span></span><span></span></div>
  <div class="brand"><div class="brand-dot"></div><div>Pinegate<br>Lark Group</div></div>
  <div class="header-call">
    <div class="phone-badge"><svg width="16" height="16" viewBox="0 0 24 24"><path fill="#fff" d="M6.6 10.8a15 15 0 0 0 6.6 6.6l2.2-2.2c.3-.3.7-.4 1-.2 1.1.4 2.3.6 3.6.6.6 0 1 .4 1 1V20c0 .6-.4 1-1 1A17 17 0 0 1 3 4c0-.6.4-1 1-1h3.5c.6 0 1 .4 1 1 0 1.3.2 2.5.6 3.6.1.3 0 .7-.2 1z"/></svg></div>
    <div>Confidential Financial<br>Review <b>Call Now</b><br>555.014.2290</div>
  </div>
</header>

<section class="hero" role="img" aria-label="Hand holding a tablet with a glowing rising stock candlestick chart">
  <svg class="hero-arrow prev" width="20" height="32" viewBox="0 0 20 32"><path d="M16 3 4 16l12 13" stroke="#fff" stroke-width="4" fill="none"/></svg>
  <div class="hero-title">Services That Save</div>
  <svg class="hero-arrow next" width="20" height="32" viewBox="0 0 20 32"><path d="M4 3l12 13L4 29" stroke="#fff" stroke-width="4" fill="none"/></svg>
  <div class="dots"><i class="on"></i><i></i><i></i><i></i></div>
</section>

<section class="services">
  <div>
    <h2>Our Services:</h2>
    <ul class="service-list">
      <li><svg width="16" height="16" viewBox="0 0 16 16"><rect x="1" y="1" width="14" height="14" fill="none" stroke="#999"/><path d="M3 8l4 4 8-10" stroke="#ed1c24" stroke-width="2.2" fill="none"/></svg>Tax Strategy</li>
      <li><svg width="16" height="16" viewBox="0 0 16 16"><rect x="1" y="1" width="14" height="14" fill="none" stroke="#999"/><path d="M3 8l4 4 8-10" stroke="#ed1c24" stroke-width="2.2" fill="none"/></svg>Predictable Retirement Solutions</li>
      <li><svg width="16" height="16" viewBox="0 0 16 16"><rect x="1" y="1" width="14" height="14" fill="none" stroke="#999"/><path d="M3 8l4 4 8-10" stroke="#ed1c24" stroke-width="2.2" fill="none"/></svg>Business Tax Avoidance</li>
      <li><svg width="16" height="16" viewBox="0 0 16 16"><rect x="1" y="1" width="14" height="14" fill="none" stroke="#999"/><path d="M3 8l4 4 8-10" stroke="#ed1c24" stroke-width="2.2" fill="none"/></svg>Liability</li>
      <li><svg width="16" height="16" viewBox="0 0 16 16"><rect x="1" y="1" width="14" height="14" fill="none" stroke="#999"/><path d="M3 8l4 4 8-10" stroke="#ed1c24" stroke-width="2.2" fill="none"/></svg>Legacy Planning</li>
      <li><svg width="16" height="16" viewBox="0 0 16 16"><rect x="1" y="1" width="14" height="14" fill="none" stroke="#999"/><path d="M3 8l4 4 8-10" stroke="#ed1c24" stroke-width="2.2" fill="none"/></svg>Superior College Saving Plans</li>
      <li><svg width="16" height="16" viewBox="0 0 16 16"><rect x="1" y="1" width="14" height="14" fill="none" stroke="#999"/><path d="M3 8l4 4 8-10" stroke="#ed1c24" stroke-width="2.2" fill="none"/></svg>Fee-less Portfolio Management</li>
      <li><svg width="16" height="16" viewBox="0 0 16 16"><rect x="1" y="1" width="14" height="14" fill="none" stroke="#999"/><path d="M3 8l4 4 8-10" stroke="#ed1c24" stroke-width="2.2" fill="none"/></svg>Market Crash Protection</li>
    </ul>
  </div>
  <svg class="chart" viewBox="0 0 516 336" font-family="Roboto, Arial, sans-serif">
    <g stroke="#e4e4e4">
      <line x1="48" y1="60" x2="48" y2="300"/><line x1="48" y1="300" x2="500" y2="300"/>
      <line x1="48" y1="90" x2="500" y2="90"/><line x1="48" y1="150" x2="500" y2="150"/><line x1="48" y1="210" x2="500" y2="210"/><line x1="48" y1="260" x2="500" y2="260"/>
      <line x1="123" y1="60" x2="123" y2="300"/><line x1="198" y1="60" x2="198" y2="300"/><line x1="274" y1="60" x2="274" y2="300"/><line x1="349" y1="60" x2="349" y2="300"/><line x1="424" y1="60" x2="424" y2="300"/><line x1="500" y1="60" x2="500" y2="300"/>
    </g>
    <g font-size="11" fill="#333">
      <text x="16" y="94">$2m</text><text x="12" y="154">$1.5m</text><text x="12" y="214">$1.0m</text><text x="12" y="264">$500k</text>
      <text x="45" y="320">0</text><text x="120" y="320">5</text><text x="192" y="320">10</text><text x="268" y="320">15</text><text x="343" y="320">20</text><text x="418" y="320">25</text><text x="494" y="320">30</text>
    </g>
    <path d="M48 298 C250 290 400 250 500 88" stroke="#f05a1a" stroke-width="2.5" fill="none"/>
    <path d="M48 298 C260 292 410 262 500 128" stroke="#3aaa3a" stroke-width="2.5" fill="none"/>
    <path d="M48 298 C270 294 420 272 500 162" stroke="#3a86e8" stroke-width="2.5" fill="none"/>
    <path d="M48 298 C280 296 430 286 500 208" stroke="#222" stroke-width="2.5" fill="none"/>
    <g font-size="9" fill="#fff" text-anchor="middle">
      <rect x="358" y="36" width="128" height="30" fill="#f05a1a"/><text x="422" y="48">Total Value $2,540,730</text><text x="422" y="60">8% Return · No Fees</text>
      <rect x="302" y="82" width="126" height="30" fill="#3aaa3a"/><text x="365" y="94">Total Value $1,730,779</text><text x="365" y="106">8% Return · 1% Fees</text>
      <rect x="240" y="128" width="124" height="30" fill="#3a86e8"/><text x="302" y="140">Total Value $1,402,566</text><text x="302" y="152">8% Return · 2% Fees</text>
      <rect x="130" y="178" width="124" height="30" fill="#333"/><text x="192" y="190">Total Value $1,134,066</text><text x="192" y="202">8% Return · 3% Fees</text>
    </g>
  </svg>
</section>

<section class="contact-band">
  <h3>Contact us at Sales</h3>
  <div class="contact-row">
    <span><span class="phone-badge"><svg width="26" height="20" viewBox="0 0 26 20"><rect x="1" y="1" width="24" height="18" fill="#fff"/><path d="M1 1l12 10L25 1" stroke="#ed1c24" stroke-width="2" fill="none"/></svg></span>Sales@PinegateLarkGroup.com</span>
    <span><span class="phone-badge"><svg width="26" height="26" viewBox="0 0 24 24"><path fill="#fff" d="M6.6 10.8a15 15 0 0 0 6.6 6.6l2.2-2.2c.3-.3.7-.4 1-.2 1.1.4 2.3.6 3.6.6.6 0 1 .4 1 1V20c0 .6-.4 1-1 1A17 17 0 0 1 3 4c0-.6.4-1 1-1h3.5c.6 0 1 .4 1 1 0 1.3.2 2.5.6 3.6.1.3 0 .7-.2 1z"/></svg></span>555.014.2290</span>
  </div>
  <small>Secure Your 401 K</small>
</section>

<section class="strategies">
  <h2 class="section-title">Tax Strategies Accountants &amp; Financial Advisors Don't Have</h2>
  <div class="strategy-grid">
    <div class="strategy-card"><svg width="46" height="40" viewBox="0 0 46 40"><g fill="#ed1c24"><rect x="4" y="22" width="6" height="16"/><rect x="14" y="14" width="6" height="24"/><rect x="24" y="18" width="6" height="20"/><rect x="34" y="6" width="6" height="32"/></g><path d="M2 38h42" stroke="#ed1c24" stroke-width="2"/></svg>Insuring Portfolios Against Market Crashes</div>
    <div class="strategy-card"><svg width="40" height="40" viewBox="0 0 40 40"><circle cx="20" cy="20" r="17" fill="none" stroke="#ed1c24" stroke-width="3"/><path d="M20 9v12l8 5" stroke="#ed1c24" stroke-width="3" fill="none"/></svg>Seemingly Small Fees Devastate Retirements.</div>
    <div class="strategy-card"><svg width="46" height="40" viewBox="0 0 46 40"><rect x="3" y="3" width="40" height="34" fill="none" stroke="#ed1c24" stroke-width="3"/><rect x="3" y="3" width="40" height="10" fill="#ed1c24"/><path d="M10 21h26M10 28h18" stroke="#ed1c24" stroke-width="3"/></svg>Business Owners &amp; Executives Love Our Tax &amp; Bonus Strategies!</div>
    <div class="strategy-card"><svg width="40" height="40" viewBox="0 0 40 40"><circle cx="20" cy="20" r="17" fill="#ed1c24"/><text x="20" y="27" font-size="20" font-family="Roboto, Arial, sans-serif" font-weight="700" fill="#fff" text-anchor="middle">$</text></svg>401K, Mutual Fund &amp; IRA Myths Revealed</div>
  </div>
</section>

<div class="dark-band">Blogs, Videos &amp; Radio</div>

<section class="blogs">
  <div class="blog-grid">
    <article class="blog-card">
      <div class="blog-media" role="img" aria-label="Radio station brand panel" style="background:#e9e9e9"></div>
      <h4>Northwave Radio</h4>
      <p>Catch us on Northwave Radio's Dana Morrow Show<br>KVLR Talk 710 am<br>(Money Minded Max &amp; Everyday Al)</p>
    </article>
    <article class="blog-card">
      <div class="blog-media" role="img" aria-label="Advisor portrait in an office" style="background:linear-gradient(135deg,#c9ced3,#8a96a3)"></div>
      <h4>PLG Videos</h4>
      <p>Lorem Ipsum is simply dummy the printing and typesetting industry. Lorem Ipsum has been the in the standard dummy.</p>
    </article>
    <article class="blog-card">
      <div class="blog-media" role="img" aria-label="Businessman celebrating under falling banknotes" style="background:linear-gradient(180deg,#e6e8ea,#a7aeb5)"></div>
      <h4>Money Blog</h4>
      <p>Ever start to think that portfolio and investing is so confusing that you need a financial advisor to help them to your money? Maybe it's by design. Get educated on our blog. Time to get in touch, stay in touch and get educated about your money. Your education is our advantage. Check out our extremely educational and entertaining Money Series with Money Minded Max and Everyday Al.</p>
    </article>
  </div>
  <span class="pill">401k Facts</span>
</section>

<div class="dark-band">Testimonials</div>

<section class="testimonials">
  <div class="testimonial-grid">
    <div class="testimonial"><div class="avatar" role="img" aria-label="Client portrait"></div><h5>Ted Walsh</h5><p>Valley Business Council Turnaround CEO of the Year<br>I'm a CFO by trade. PLG has strategies for families, executive &amp; business owners that accountants and financial advisors don't have. Highest recommendation</p></div>
    <div class="testimonial"><div class="avatar" role="img" aria-label="Client portrait"></div><h5>Jon Hale</h5><p>Probate Attorney. As an attorney, my job is to weigh risk. As an investor, weighing risk and reward is even more important. As someone retiring in next 15 years, I wanted to eliminate the risks of a stock market crash. PLG does this better than any other company.</p></div>
    <div class="testimonial"><div class="avatar" role="img" aria-label="Client portrait"></div><h5>Gary Lenz</h5><p>Doctor. Being a doctor requires attention to detail. Pinegate Lark Group helped navigate and educate me on exactly how to decipher my portfolio statement. I would have changed 10 years ago if I would have known what I know now about money. Call them; you'll be happy you did</p></div>
  </div>
  <div class="dots"><i class="on"></i><i></i><i></i></div>
  <div class="subscribe"><div class="field">Shoot us a quick email here</div><span class="pill">Submit</span></div>
  <div class="call-us">CALL US <span class="phone-badge"><svg width="28" height="28" viewBox="0 0 24 24"><path fill="#fff" d="M6.6 10.8a15 15 0 0 0 6.6 6.6l2.2-2.2c.3-.3.7-.4 1-.2 1.1.4 2.3.6 3.6.6.6 0 1 .4 1 1V20c0 .6-.4 1-1 1A17 17 0 0 1 3 4c0-.6.4-1 1-1h3.5c.6 0 1 .4 1 1 0 1.3.2 2.5.6 3.6.1.3 0 .7-.2 1z"/></svg></span> 555.014.2290</div>
</section>

<footer class="site-footer">
  <div class="footer-brand">
    <div class="brand"><div class="brand-dot"></div><div>Pinegate<br>Lark Group</div></div>
    <p>Bringing sensibility, predictability and peace of mind in retirement. We will do things for your financial lives accountants and financial advisors won't and can't.</p>
  </div>
  <div class="footer-col links"><h6>Quick Link</h6><ul><li>Home</li><li>Insuring Portfolios</li><li>Small Fees</li><li>Business Owners</li><li>401K</li><li>Services</li><li>Contact us</li></ul></div>
  <div class="footer-col address"><h6>Address</h6>
    <p><span>⌖</span><span>4820 Orchard Lane,<br>Maple Hill,<br>CA 95000</span></p>
    <p><span>✆</span><span>555.014.2290</span></p>
    <p><span>✉</span><span>Sales@PinegateLarkGroup.com</span></p>
  </div>
  <div class="footer-col contact-form"><h6>Contact us</h6>
    <div class="form-row"><div>Name</div><div>Email</div><div>Phone</div></div>
    <div class="form-msg">Message</div>
    <span class="pill">Baby Boomer Edition</span>
  </div>
</footer>
<div class="copyright"><span>CopyRight © 2019 Pinegate Lark Group. All Right Reserve</span><div class="social"><i></i><i></i><i></i><i></i><i></i></div></div>
</body>
</html>
```